Cannabis Media Network Advertising Kit

Polar Orbit Media is a digital media news network focused on the startups, entrepreneurs and innovative companies in the cannabis industry. We are ready to release our new services for 2017.

We are looking for a modern looking advertising kit created that we would send to our potential clients.

We want it to look similar to our branding. Our website is www.polarorbitmedia.example.

Target Market(s)

Page 3: Audience:
Entrepreneurs, professionals, execs, VC’s, and Investors
Include stats: 34% Female/ 66% Male, 34% 25-34 Years Old $24% 35-44 Years Old

Industry/Entity Type

Media

Font styles to use
Sans Serif

Colors
0555a3
0492cd
ffffff
edf1f7

Requirements
Must have
• Outline Idea is below. Images can be provided.
• Page 1: Header Page (POM logo)
• Leading digital media news network covering the latest tech, startups, and innovative companies in the cannabis industry.
• Page 2: About Us - Mission and Brand
• Polar Orbit Media is the leading digital media platform that is dedicated to profiling the startups, entrepreneurs and innovative companies in the cannabis industry.
• Over the past few years we have been highlighting the upcoming and established businesses in the industry, developed a platform for leaders to share their knowledge and insight, and created
• a spotlight for the innovative technology.
• But most importantly, we have created a community of entrepreneurs, investors and professionals who have the same mission of growing the b2b industry together.
• POM is more than just a network and brand, we are highlighting history in the making of high quality original content.
• Page 3: Audience:
• Entrepreneurs, professionals, execs, VC’s, and Investors
• Include stats: 34% Female/ 66% Male, 34% 25-34 Years Old $24% 35-44 Years Old
• Page 4: POM Original Web Series
• Pre/Post Commercial Opportunities $5,000
• Tinbell Reviews and POM Talks
• Tinbell Reviews is a un-biased product review segment for the wholesalers, online stores, dispensaries and more.
• POM Talks: One on one interview with the upcoming and leading founders offering advice and insight for fellow entrepreneurs.
• Page 5: POM Original Web Series
• Kettles and Kites is a female founder focused web series, where we highlight the leaders, discuss informative topics and latest products.
• Product placement $2,500
• Page 6: POM Original Web Series
• Upside Ledge gives you a peek into the entrepreneur 2.0 and what it is like running a cannabis business.
• See leadership package
• Page 7: Package 1: Foundation $1,000
• 1. Four full platform ads (via QT, ZR, Plonkit, Fernwork, Braxtile)
• 2. POM Article/Company Spotlight (One Newsletter feature and full POM promotion)
• 3. Newsletter Ad (One run, assets provided by client
• Page 8: Package 2: Traction $5,000
• 1. Six full platform ads (via QT, ZR, Plonkit, Fernwork, Braxtile)
• 4. Business of the Month Badge (POM Homepage)
• 5. Three Verbal Video Advertisements ( Three segments, up to 10 seconds each)
• Page 9: Package 3: Leadership $15,000
• 5. Three Video Advertisements (Three segments, 30 second commercial)
• 7. Upside Ledge Full Segment
• Includes promo and full segment promoted and released via POM.
• Page 10: Events Promotion
• Event Package $1,000
• 1. Four full platform ads (via QT include QT Event on POM Page, ZR, Plonkit, Fernwork, Braxtile)
• A la Carte:
• Add event to POM calendar, basic promotion via social media $250
• POMTV Media Sponsor
• Includes co-branded video production of event, exclusive interview with sponsors, and more
• *Cost: To Be Determined
• Page 11: A La Carte
• 1. Event Addition to Calendar (Basic promotion via social media)
• 2. Six full platform ads (via QT, ZR, Plonkit, Fernwork, Braxtile)
• 3. POM Article/Company Spotlight (One Newsletter feature and full POM promotion)
• 4. Newsletter Ad (One run, assets provided by client
• 5. Business of the Month Badge (POM Homepage)
• 6. Three Verbal Video Advertisements ( Three segments, up to 10 seconds each)
• Page 12: Traction
• Profiled on fernwork, orbel daily, spindara, quillstoa, plonkit, zephrame
• 10k+ organic email list of professionals
• 16k+ page views increasing 25% each month
• 18k+ social media followers
• Viewed in all 50 states and 98 countries
• Page 13: Message from the CEO
• “We at POM understand that our industry is different than any other industry out there, we even look at the entrepreneurs and don’t see them just as an entrepreneur but as an entrepreneur 2.0. Why? Because this is the first time in a long time where we have the opportunity to change how an industry is built from the foundation up and each of these individuals are faced with hurdles and challenges we wouldn’t face in any other industry and yet they are doing what it takes to continue to move forward.”
• Page 14: Contact Us
• POM logo:
• We look forward to growing your brand with the Polar Orbit Media! Contact us today at contact@polarorbitmedia.example
Nice to have
• High Res Images from our content. Which we can provide those images, or you can pull from our site and we can send high res after.
Should not have
• Dark Designed.

```html
<!DOCTYPE html>
<html lang="en">
<head>
<meta charset="utf-8">
<title>Kettles and Kites – Polar Orbit Media Advertising Kit</title>
<link href="https://fonts.googleapis.com/css2?family=Open+Sans:wght@300;400;600;700&display=swap" rel="stylesheet">
<style>
  :root {
    --navy: #0555a3;
    --sky: #0492cd;
    --white: #ffffff;
    --paper: #edf1f7;
    --ink: #2b2b2b;
  }
  html, body {
    margin: 0;
    padding: 0;
    overflow: hidden;
    background: var(--paper);
  }
  .page {
    position: relative;
    width: 1200px;
    height: 900px;
    overflow: hidden;
    background: var(--paper);
    font-family: "Open Sans", sans-serif;
  }
  .corner-art {
    position: absolute;
    left: 0;
    top: 0;
  }
  .series-title {
    position: absolute;
    left: 52px;
    top: 176px;
    width: 200px;
    margin: 0;
    text-align: center;
    color: var(--navy);
    font-weight: 700;
    font-size: 28px;
    line-height: 30px;
    letter-spacing: -0.3px;
  }
  .episode-frame {
    position: absolute;
    left: 448px;
    top: 92px;
    width: 472px;
    height: 303px;
    border: 1.5px solid var(--sky);
    background: var(--white);
    box-sizing: border-box;
  }
  .episode-still {
    position: absolute;
    left: 11px;
    top: 11px;
    right: 11px;
    bottom: 11px;
    background: linear-gradient(160deg, #9bb38a 0%, #c9c4b9 35%, #8f8a86 70%, #b7603c 100%);
  }
  .series-copy {
    position: absolute;
    left: 447px;
    top: 443px;
    width: 480px;
    margin: 0;
    padding: 0;
    list-style: none;
  }
  .series-copy li {
    position: relative;
    padding-left: 14px;
    color: var(--ink);
    font-weight: 300;
    font-size: 19px;
    line-height: 33.6px;
  }
  .series-copy li::before {
    content: "";
    position: absolute;
    left: 0;
    top: 14px;
    width: 6px;
    height: 6px;
    border-radius: 50%;
    background: var(--sky);
  }
  .offer {
    position: absolute;
    left: 448px;
  }
  .offer-label {
    margin: 0;
    color: var(--navy);
    font-weight: 600;
    font-size: 19.5px;
    line-height: 24px;
  }
  .offer-price {
    margin: 2px 0 0;
    color: var(--sky);
    font-weight: 600;
    font-size: 37px;
    line-height: 44px;
  }
  .offer-placement { top: 580px; }
  .offer-commercial { top: 692px; }
  .corner-foot {
    position: absolute;
    right: 0;
    bottom: 0;
  }
  .brand-mark {
    position: absolute;
    left: 1100px;
    top: 808px;
    color: var(--navy);
    font-weight: 700;
    font-size: 17px;
    letter-spacing: 0.5px;
  }
  .page-number {
    position: absolute;
    left: 1150px;
    top: 848px;
    color: var(--ink);
    font-weight: 400;
    font-size: 17px;
  }
</style>
</head>
<body>
<main class="page">
  <svg class="corner-art" width="320" height="410" viewBox="0 0 320 410" aria-hidden="true">
    <defs>
      <linearGradient id="facet" x1="0" y1="0" x2="1" y2="1">
        <stop offset="0" stop-color="#1d6fc0"/>
        <stop offset="0.5" stop-color="#3c93d8"/>
        <stop offset="1" stop-color="#1a64b5"/>
      </linearGradient>
    </defs>
    <polygon points="0,0 262,0 205,74 60,300 0,390" fill="url(#facet)"/>
    <circle cx="152" cy="202" r="150" fill="var(--white)"/>
    <circle cx="152" cy="202" r="145" fill="url(#facet)"/>
    <polygon points="40,60 150,20 120,110" fill="#ffffff" opacity="0.07"/>
    <polygon points="200,250 290,200 260,320" fill="#000000" opacity="0.06"/>
    <circle cx="152" cy="202" r="102" fill="var(--white)"/>
    <line x1="274" y1="0" x2="214" y2="72" stroke="var(--navy)" stroke-width="5"/>
    <line x1="54" y1="306" x2="0" y2="398" stroke="var(--sky)" stroke-width="5"/>
  </svg>

  <h1 class="series-title">KETTLES &amp;<br>KITES</h1>

  <figure class="episode-frame">
    <div class="episode-still" role="img" aria-label="Photo: four hosts seated on a sofa chatting during an episode of Kettles and Kites"></div>
  </figure>

  <ul class="series-copy">
    <li>Kettles and Kites is a female founder focused web series, where we highlight the leaders, discuss informative topics and the latest products.</li>
  </ul>

  <section class="offer offer-placement">
    <p class="offer-label">Product placement</p>
    <p class="offer-price">$2,500</p>
  </section>

  <section class="offer offer-commercial">
    <p class="offer-label">Pre/Post Commercial Opportunities</p>
    <p class="offer-price">$5,000</p>
  </section>

  <svg class="corner-foot" width="140" height="200" viewBox="0 0 140 200" aria-hidden="true">
    <line x1="142" y1="10" x2="92" y2="92" stroke="var(--sky)" stroke-width="5"/>
    <line x1="54" y1="148" x2="12" y2="202" stroke="var(--sky)" stroke-width="5"/>
  </svg>
  <span class="brand-mark">POM</span>
  <span class="page-number">5</span>
</main>
</body>
</html>
```